New, modern business card for growing audiology practice

We need a new business card for our audiology practice. Our logo and website have recently changed (more modern) and we want our business cards to reflect this change.
We conduct hearing tests, perform earwax removals, and fit & dispense hearing aids to our patients. We are a family owned practice in which the owner is the one who works directly with the patient. I have attached logos in various formats to use, as well as two ideas I found on this website; as well as a scanned copy of our current logo. Good luck!

Industry/Entity Type

Business

Contact Information for Business Card

Company name: Tolvera Hearing Center
Provider name: Peter Wolstenby, Au.D. F/NSB
Phone number: (440) 683-5127
Address: 837 W. Lindell Ave. Brenholt Falls, OH 44071
email: tolverahearing@postvane.com
website: tolverahearing.com

Colors
000000
aaaaaa
dbdbdb
cacaca
9bcb3c
afd23c
cadf82
b1b1b1

Requirements
Must have
• My card must include information in the "details" section. In the attached images, I found a few that I liked and I would like to model after - "brisky bouncin'" and "Sound Method Center".
• Must be horizontal.
• Must include logos provided. I uploaded them in various file formats and various ways.
• Must match logo font, if possible, if not, please get as close as you can.
Nice to have
• I really like the idea of having a color on one side with just the logo and company name and the contact information and provider name on the other side. I also really like the idea of having the main color dominating on the logo/company side with accent of that same color on the contact side of the card.
Should not have
• Must not be vertical.

```html
<!DOCTYPE html>
<html lang="en">
<head>
<meta charset="utf-8">
<title>Tolvera Hearing Center – Business Card</title>
<link rel="stylesheet" href="https://fonts.googleapis.com/css2?family=Lato:wght@400&family=Roboto:wght@400;700&display=swap">
<style>
  :root {
    --backdrop: #e6e6e4;
    --card: #f5f5f3;
    --card-edge: #dbdbdb;
    --brand-green: #6fa83d;
    --ink: #1c1c1c;
    --ink-soft: #333333;
  }
  html, body {
    margin: 0;
    padding: 0;
    width: 1200px;
    height: 969px;
    overflow: hidden;
    background: var(--backdrop);
  }
  .canvas {
    position: relative;
    width: 1200px;
    height: 969px;
  }
  .card {
    position: absolute;
    left: 100px;
    top: 200px;
    width: 1000px;
    height: 570px;
    background: var(--card);
    border: 1px solid var(--card-edge);
    border-radius: 34px;
    overflow: hidden;
    box-shadow: 0 18px 40px rgba(0,0,0,0.12);
  }
  .brand-band {
    position: absolute;
    left: 0;
    top: 0;
    width: 362px;
    height: 100%;
    background: var(--brand-green);
  }
  .wordmark {
    position: absolute;
    right: 52px;
    top: 62px;
    display: flex;
    align-items: center;
    gap: 16px;
    font-family: "Lato", sans-serif;
    font-weight: 400;
    font-size: 33px;
    letter-spacing: 0.5px;
    color: var(--ink);
    text-transform: uppercase;
    white-space: nowrap;
  }
  .wordmark-dot {
    width: 26px;
    height: 26px;
    border-radius: 50%;
    background: var(--brand-green);
  }
  .details {
    position: absolute;
    right: 52px;
    top: 250px;
    text-align: right;
    font-family: "Roboto", sans-serif;
    color: var(--ink-soft);
    white-space: nowrap;
  }
  .provider-name {
    margin: 0;
    font-size: 32px;
    font-weight: 700;
    color: var(--brand-green);
    text-transform: uppercase;
    line-height: 1.15;
  }
  .provider-credentials {
    margin: 2px 0 0;
    font-size: 24px;
    font-weight: 700;
    color: var(--ink);
    text-transform: uppercase;
  }
  .address {
    margin: 24px 0 0;
    font-size: 24px;
    line-height: 1.3;
    font-style: normal;
  }
  .contact-list {
    list-style: none;
    margin: 20px 0 0;
    padding: 0;
    font-size: 24px;
    line-height: 1.38;
  }
  .contact-list li {
    display: flex;
    justify-content: flex-end;
    align-items: center;
    gap: 18px;
  }
  .contact-icon {
    width: 20px;
    height: 20px;
    flex: none;
    fill: var(--brand-green);
  }
</style>
</head>
<body>
<div class="canvas">
  <div class="card">
    <div class="brand-band"></div>

    <div class="wordmark">
      <span class="wordmark-dot"></span>
      <span>Tolvera Hearing Center</span>
    </div>

    <div class="details">
      <h1 class="provider-name">Peter Wolstenby</h1>
      <p class="provider-credentials">Au.D. F/NSB</p>
      <address class="address">
        837 W. Lindell Ave.<br>
        Brenholt Falls, OH 44071
      </address>
      <ul class="contact-list">
        <li>
          <span>(440) 683-5127</span>
          <svg class="contact-icon" viewBox="0 0 24 24" aria-hidden="true"><path d="M6.6 10.8a15.1 15.1 0 0 0 6.6 6.6l2.2-2.2c.3-.3.7-.4 1-.2 1.1.4 2.3.6 3.6.6.6 0 1 .4 1 1V20c0 .6-.4 1-1 1A17 17 0 0 1 3 4c0-.6.4-1 1-1h3.5c.6 0 1 .4 1 1 0 1.3.2 2.5.6 3.6.1.3 0 .7-.2 1z"/></svg>
        </li>
        <li>
          <span>tolverahearing@postvane.com</span>
          <svg class="contact-icon" viewBox="0 0 24 24" aria-hidden="true"><path d="M2 5h20v14H2z"/><path d="M3 6l9 6.3L21 6" fill="none" stroke="#f5f5f3" stroke-width="1.6"/></svg>
        </li>
        <li>
          <span>tolverahearing.com</span>
          <svg class="contact-icon" viewBox="0 0 24 24" aria-hidden="true"><circle cx="12" cy="12" r="10"/><path d="M2 12h20M12 2c3 3 3 17 0 20M12 2c-3 3-3 17 0 20" fill="none" stroke="#f5f5f3" stroke-width="1.4"/></svg>
        </li>
      </ul>
    </div>
  </div>
</div>
</body>
</html>
```